Coastline Premier Retreats Business Card Design

Design a business card for Coastline Premier Retreats. Look at the website for colors and reference. Card should have logo, name, title, office number, mobile number, email, URL and a tagline like, "Luxury Hotel & Resort Email Marketing" (This might change).

https://www.coastlinepremierretreats.example

The rest I will leave up to your imagination.

Contact Information for Business Card

Logo, name, title, office number, mobile number, email, URL and a tagline like, "Luxury Hotel & Resort Email Marketing" (This might change).

```html
<!DOCTYPE html>
<html lang="en">
<head>
<meta charset="UTF-8">
<title>Coastline Premier Retreats – Business Card</title>
<link rel="stylesheet" href="https://fonts.googleapis.com/css2?family=Lato:wght@300;400;700&display=swap">
<style>
  :root {
    --backdrop: #2a2a2a;
    --card: #ffffff;
    --card-shade: #e9e9e9;
    --accent: #ee7423;
    --ink: #1a1a1a;
    --muted: #666666;
  }
  * { box-sizing: border-box; margin: 0; padding: 0; }
  html, body { width: 1200px; height: 900px; overflow: hidden; }
  body {
    background: var(--backdrop);
    font-family: 'Lato', sans-serif;
    display: flex;
    flex-direction: column;
    align-items: center;
    justify-content: center;
    gap: 60px;
  }
  .card {
    position: relative;
    width: 600px;
    height: 343px;
    background: linear-gradient(110deg, var(--card-shade) 0%, var(--card) 55%);
    overflow: hidden;
  }
  .card__band {
    position: absolute;
    left: 0; right: 0; bottom: 0;
    height: 12px;
    background: var(--accent);
  }
  .brand {
    display: flex;
    align-items: center;
    gap: 10px;
    font-weight: 700;
    color: var(--ink);
    text-transform: uppercase;
    letter-spacing: 0.04em;
  }
  .brand__mark {
    width: 12px; height: 12px;
    background: var(--accent);
  }

  /* front */
  .card--front .brand {
    position: absolute;
    top: 108px; left: 0; right: 0;
    justify-content: center;
    font-size: 26px;
  }
  .card--front .rule {
    position: absolute;
    top: 190px; left: 60px; right: 60px;
    height: 1px;
    background: var(--accent);
  }
  .tagline {
    position: absolute;
    top: 210px; left: 0; right: 0;
    text-align: center;
    font-size: 19px;
    letter-spacing: 0.16em;
    color: var(--ink);
  }

  /* back */
  .card--back .brand {
    position: absolute;
    top: 40px; right: 40px;
    font-size: 20px;
  }
  .person {
    position: absolute;
    top: 120px; left: 48px;
  }
  .person__name {
    font-size: 19px;
    color: var(--accent);
    text-transform: uppercase;
    letter-spacing: 0.02em;
  }
  .person__title {
    font-size: 16px;
    color: var(--muted);
    font-weight: 300;
  }
  .contacts {
    list-style: none;
    position: absolute;
    top: 196px; left: 60px;
    font-size: 15px;
    font-weight: 300;
    color: #444;
  }
  .contacts li {
    display: flex;
    align-items: center;
    gap: 10px;
    height: 22px;
  }
  .contacts svg { width: 14px; height: 14px; fill: none; stroke: var(--accent); stroke-width: 2; }
  .contacts svg .solid { fill: var(--accent); stroke: none; }
</style>
</head>
<body>

  <section class="card card--front" aria-label="Card front">
    <div class="brand"><span class="brand__mark"></span>Coastline Premier Retreats</div>
    <div class="rule"></div>
    <p class="tagline">Luxury Hotel &amp; Resort Email Marketing</p>
    <div class="card__band"></div>
  </section>

  <section class="card card--back" aria-label="Card back">
    <div class="brand"><span class="brand__mark"></span>Coastline Premier Retreats</div>
    <div class="person">
      <p class="person__name">Marcus Hale</p>
      <p class="person__title">Director</p>
    </div>
    <ul class="contacts">
      <li>
        <svg viewBox="0 0 14 14"><rect x="3.5" y="1" width="7" height="12" rx="1"/></svg>
        555.010.4400
      </li>
      <li>
        <svg viewBox="0 0 14 14"><path class="solid" d="M2 1.5l3 0 1 3-1.6 1.2a7 7 0 0 0 3.9 3.9L9.5 8l3 1v3c0 .6-.5 1-1 1A10.5 10.5 0 0 1 1 2.5c0-.5.4-1 1-1z"/></svg>
        555.014.2200
      </li>
      <li>
        <svg viewBox="0 0 14 14"><rect x="1" y="3" width="12" height="8"/><path d="M1 3l6 5 6-5"/></svg>
        info@coastlinepremierretreats.example
      </li>
      <li>
        <svg viewBox="0 0 14 14"><circle cx="7" cy="7" r="5.5"/><path d="M1.5 7h11M7 1.5c-3 3-3 8 0 11M7 1.5c3 3 3 8 0 11"/></svg>
        www.coastlinepremierretreats.example
      </li>
      <li>
        <svg viewBox="0 0 14 14"><path class="solid" d="M7 1a4.5 4.5 0 0 0-4.5 4.5C2.5 9 7 13.5 7 13.5S11.5 9 11.5 5.5A4.5 4.5 0 0 0 7 1zm0 6.2a1.7 1.7 0 1 1 0-3.4 1.7 1.7 0 0 1 0 3.4z"/></svg>
        North America
      </li>
    </ul>
    <div class="card__band"></div>
  </section>

</body>
</html>
```